Consumer and commercial IOT solutions (Internet Of Things)

We are a startup and are looking for business cards with logo. The logo will appear on all of our media as well as our ecommerce site and social sites that have yet to be developed. We want to present a fresh face on a high tech company that innovates at every turn. You can read about our solutions on our information only web site www.plonaxhub.net - We have some wording we would like used on our business cards but there is no place for this except for here. The company name is "RM Industrial IOT" I have some samples of logos I am interested in seeing but I will let your team make the initial presentations

```html
<!DOCTYPE html>
<html lang="en">
<head>
<meta charset="utf-8">
<title>Plonax Group — Business Card</title>
<link rel="stylesheet" href="https://fonts.googleapis.com/css2?family=Montserrat:wght@300;400;600;700&family=Lato:wght@400&display=swap">
<style>
  :root {
    --backdrop: #2a2b2d;
    --card-white: #ffffff;
    --card-fade: #efefef;
    --navy: #1d2b4a;
    --navy-deep: #15213b;
    --navy-back: #1a2744;
    --blue: #4a93d0;
    --blue-mid: #3b6fa3;
    --text-dark: #1f2433;
  }
  * { margin: 0; padding: 0; box-sizing: border-box; }
  html, body { width: 1200px; height: 732px; overflow: hidden; }
  body { background: var(--backdrop); position: relative; font-family: "Lato", sans-serif; }

  .card {
    position: absolute;
    top: 242px;
    width: 436px;
    height: 248px;
    box-shadow: 0 10px 22px rgba(0,0,0,0.55);
    overflow: hidden;
  }
  .card-front {
    left: 144px;
    background: linear-gradient(180deg, var(--card-white) 0%, var(--card-fade) 100%);
  }
  .card-back { left: 621px; }

  .brand {
    position: absolute;
    display: flex;
    align-items: center;
    gap: 6px;
    white-space: nowrap;
  }
  .card-front .brand {
    left: 135px;
    top: 118px;
    transform: translateX(-50%);
  }
  .brand-square {
    width: 10px; height: 10px;
    background: var(--navy);
    flex: none;
  }
  .brand-name {
    font-family: "Montserrat", sans-serif;
    font-weight: 600;
    font-size: 14px;
    letter-spacing: 0.3px;
    color: var(--navy);
  }

  .divider {
    position: absolute;
    left: 217px; top: 78px;
    width: 1.5px; height: 100px;
    background: var(--blue);
  }

  .contact-block { position: absolute; left: 237px; top: 78px; color: var(--text-dark); }
  .person-name {
    font-family: "Montserrat", sans-serif;
    font-weight: 600;
    font-size: 17px;
    line-height: 20px;
    color: var(--navy);
  }
  .person-title { font-size: 12px; line-height: 14px; margin-bottom: 12px; }
  .contact-list { list-style: none; }
  .contact-list li {
    display: flex; align-items: center; gap: 7px;
    font-size: 12px; line-height: 14.3px;
  }
  .contact-list svg { width: 10px; height: 10px; flex: none; }

  .tagline-band {
    position: absolute;
    left: 0; top: 217px;
    width: 100%; height: 21px;
    background: linear-gradient(90deg, var(--blue) 0%, var(--blue-mid) 45%, var(--navy-deep) 100%);
    text-align: center;
    font-family: "Montserrat", sans-serif;
    font-size: 14px;
    line-height: 21px;
  }
  .tagline-band .t-lead { font-weight: 600; color: #4d97d6; }
  .tagline-band .t-mid { font-weight: 300; color: #5a8ab8; }
  .tagline-band .t-end { font-weight: 700; color: var(--navy-deep); }

  .back-field {
    position: absolute; inset: 0;
    background: linear-gradient(160deg, #1b2949 0%, var(--navy-back) 55%, #16223c 100%);
  }
  .card-back .brand { left: 40px; top: 173px; }
  .card-back .brand-square { background: #4a7fb5; width: 9px; height: 9px; }
  .card-back .brand-name { color: #4a7fb5; font-size: 12px; }
</style>
</head>
<body>

  <section class="card card-front" aria-label="Business card front">
    <div class="brand">
      <span class="brand-square"></span>
      <span class="brand-name">PLONAX GROUP</span>
    </div>

    <div class="divider"></div>

    <div class="contact-block">
      <p class="person-name">Daniel Reyes</p>
      <p class="person-title">Project Manager</p>
      <ul class="contact-list">
        <li>
          <svg viewBox="0 0 10 10"><rect x="2.5" y="0.5" width="5" height="9" rx="1" fill="none" stroke="#4a93d0" stroke-width="0.9"/></svg>
          01-555 010 234
        </li>
        <li>
          <svg viewBox="0 0 10 10"><path d="M2 1 L4 3 L3 4.5 Q4.5 6.5 5.5 7 L7 6 L9 8 L7.5 9.3 Q3 8 0.8 2.5 Z" fill="none" stroke="#4a93d0" stroke-width="0.8"/></svg>
          01-555 010 234
        </li>
        <li>
          <svg viewBox="0 0 10 10"><rect x="0.5" y="2" width="9" height="6" fill="none" stroke="#4a93d0" stroke-width="0.9"/><path d="M0.5 2 L5 5.5 L9.5 2" fill="none" stroke="#4a93d0" stroke-width="0.9"/></svg>
          daniel@plonaxhub.net
        </li>
        <li>
          <svg viewBox="0 0 10 10"><circle cx="5" cy="5" r="4.5" fill="#4a93d0"/><path d="M0.5 5 H9.5 M5 0.5 V9.5" stroke="#fff" stroke-width="0.6"/></svg>
          www.plonaxhub.net
        </li>
      </ul>
    </div>

    <div class="tagline-band">
      <span class="t-lead">RM</span> <span class="t-mid">Industrial</span> <span class="t-end">IOT</span>
    </div>
  </section>

  <section class="card card-back" aria-label="Business card back">
    <div class="back-field" role="img" aria-label="Faint repeating brand pattern on navy background"></div>
    <div class="brand">
      <span class="brand-square"></span>
      <span class="brand-name">PLONAX GROUP</span>
    </div>
  </section>

</body>
</html>
```